Support Welcome Packet Redesign

Looking to redesign our current "welcome packet" that we send to our new customers to help them understand our support service. It is currently in Microsoft Word and would like to remain in either word or publisher. Something that we can easily edit, as the content adjusts based on the customer needs. We want this document to be simple and understandable as it should be something our customers can reference at any time during our contract and easy to navigate.

Target Market(s)

Current Customers. Healthcare, Oil & Gas, Transportation, etc.

Industry/Entity Type

It Service

Font styles to use
Sans Serif

Requirements
Must have
• Table of Contents, Tavrelo Logo and current content
Nice to have
• Easy navigation. Redone final page (contact info)

```html
<!DOCTYPE html>
<html lang="en">
<head>
<meta charset="utf-8">
<title>Tavrelo Welcome Packet – Table of Contents</title>
<link href="https://fonts.googleapis.com/css2?family=PT+Sans:wght@400;700&family=Alfa+Slab+One&display=swap" rel="stylesheet">
<style>
  :root {
    --page-bg: #ffffff;
    --frame-dots: #555555;
    --brand-blue: #2c5183;
    --panel-green: #c4d69d;
    --panel-orange: #f6bf93;
    --panel-outline: #cfc3de;
    --band-peach: #fbe3d2;
    --cell-dark: #9bbb59;
    --cell-mid: #cddcb0;
    --cell-light: #e6eed8;
    --page-num: #8c8c8c;
    --white: #ffffff;
  }
  * { box-sizing: border-box; margin: 0; padding: 0; }
  html, body { width: 927px; height: 1200px; overflow: hidden; background: var(--page-bg); }
  .page {
    position: relative;
    width: 927px; height: 1200px;
    font-family: "PT Sans", Arial, sans-serif;
    overflow: hidden;
  }
  .page-frame {
    position: absolute; inset: 22px 12px 12px 40px;
    border: 1.5px dotted var(--frame-dots);
  }
  .title-band {
    position: absolute; left: 600px; top: 44px; width: 310px; height: 112px;
    background: linear-gradient(90deg, rgba(251,227,210,0) 0%, var(--band-peach) 45%, var(--band-peach) 100%);
  }
  .page-title {
    position: absolute; right: 52px; top: 62px;
    font-size: 60px; font-weight: 700; color: var(--brand-blue);
    letter-spacing: 0.5px;
  }
  .brand {
    position: absolute; left: 86px; top: 150px;
    display: flex; align-items: center; gap: 12px;
  }
  .brand-mark { width: 26px; height: 26px; background: var(--brand-blue); }
  .brand-name { font-size: 34px; font-weight: 700; color: var(--brand-blue); line-height: 1; }
  .panel-shapes { position: absolute; left: 0; top: 0; }
  .contents {
    position: absolute; left: 59px; top: 294px; width: 799px;
    border-collapse: collapse;
  }
  .contents td, .contents th { border: 2px solid var(--white); }
  .contents-title {
    background: var(--cell-dark);
    height: 85px;
    font-size: 44px; font-weight: 700; color: var(--brand-blue);
    text-align: center;
  }
  .contents-entry {
    width: 400px; height: 47px;
    background: var(--cell-dark);
    color: var(--white); font-weight: 700; font-size: 19px;
    vertical-align: top; padding-top: 5px;
  }
  .level-1 { padding-left: 10px; }
  .level-2 { padding-left: 22px; }
  .level-3 { padding-left: 34px; }
  .contents-page {
    font-family: "Alfa Slab One", Georgia, serif;
    color: var(--page-num); font-size: 31px;
    text-align: right; vertical-align: bottom; padding: 0 10px 0 0;
    line-height: 1.2;
  }
  .tone-mid { background: var(--cell-mid); }
  .tone-light { background: var(--cell-light); }
  .support-illustration {
    position: absolute; left: 641px; top: 955px; width: 255px; height: 200px;
    border-radius: 40px;
    background: radial-gradient(ellipse at 55% 40%, rgba(74,143,212,0.75) 0%, rgba(142,197,91,0.6) 45%, rgba(246,191,147,0) 75%);
  }
</style>
</head>
<body>
<div class="page">
  <svg class="panel-shapes" width="927" height="1200" viewBox="0 0 927 1200" aria-hidden="true">
    <path d="M466 158 Q466 150 520 150 L880 150 Q905 150 905 175 L905 1180 L466 1180 Z" fill="none" stroke="#fbe3d2" stroke-width="8"/>
    <path d="M480 250 Q480 168 560 168 L868 168 Q906 168 906 206 L906 1155 Q906 1187 874 1187 L510 1187 Q480 1187 480 1157 Z" fill="var(--panel-orange)"/>
    <path d="M34 262 Q34 250 46 250 L432 250 Q474 250 474 292 L474 1150 Q474 1187 437 1187 L72 1187 Q34 1187 34 1150 Z" fill="var(--panel-green)"/>
    <path d="M40 250 L430 250 Q480 250 480 300 L480 1140" fill="none" stroke="var(--panel-outline)" stroke-width="5"/>
  </svg>

  <div class="page-frame"></div>
  <div class="title-band"></div>
  <h1 class="page-title">Welcome</h1>

  <div class="brand">
    <span class="brand-mark"></span>
    <span class="brand-name">Tavrelo</span>
  </div>

  <table class="contents">
    <tr><th class="contents-title" colspan="2">Table of Contents</th></tr>
    <tr><td class="contents-entry level-1">Document Summary</td><td class="contents-page tone-mid">2</td></tr>
    <tr><td class="contents-entry level-1">Services Summary</td><td class="contents-page tone-light">3</td></tr>
    <tr><td class="contents-entry level-1">Support Information</td><td class="contents-page tone-mid">4</td></tr>
    <tr><td class="contents-entry level-2">Tavrelo Support Teams and Escalation Path</td><td class="contents-page tone-light">4 to 5</td></tr>
    <tr><td class="contents-entry level-2">Tavrelo Support Escalation Matrix</td><td class="contents-page tone-mid">6</td></tr>
    <tr><td class="contents-entry level-3">Priority Level</td><td class="contents-page tone-light">6 to 7</td></tr>
    <tr><td class="contents-entry level-3">Escalation Guidelines</td><td class="contents-page tone-mid">8 to 9</td></tr>
    <tr><td class="contents-entry level-2">Tavrelo Support Contact Information</td><td class="contents-page tone-light">10</td></tr>
    <tr><td class="contents-entry level-2">Tavrelo Support</td><td class="contents-page tone-mid">11</td></tr>
  </table>

  <div class="support-illustration" role="img" aria-label="Illustration of a desktop computer with colourful swooshing cables and arrows"></div>
</div>
</body>
</html>
```